Vantiqo custom business card design

Need a authentic, innovative business card design for a new mobile app business. I am uploading a few screen images from our app for you to view. I would like app design theme to match business card design. I can also send logo images.

```html
<!DOCTYPE html>
<html lang="en">
<head>
<meta charset="utf-8">
<title>Vantiqo business card</title>
<link rel="stylesheet" href="https://fonts.googleapis.com/css2?family=Work+Sans:wght@400;500;700&display=swap">
<style>
  :root {
    --backdrop: #8b6b47;
    --card-dark: #1f1f1f;
    --card-light: #ffffff;
    --brand-purple: #5e2a8c;
    --text-light: #f2f2f2;
    --text-dark: #1f1f1f;
  }
  html, body {
    margin: 0;
    width: 1200px;
    height: 930px;
    overflow: hidden;
    background: var(--backdrop);
    font-family: "Work Sans", sans-serif;
  }
  .card {
    position: absolute;
    left: 318px;
    width: 564px;
    height: 322px;
    border-radius: 16px;
    background: var(--card-dark);
    overflow: hidden;
    box-shadow: 0 6px 14px rgba(0,0,0,0.35);
  }
  .card--front { top: 125px; }
  .card--back { top: 514px; }
  .front-panel {
    position: absolute;
    inset: 0;
  }
  .contact {
    position: absolute;
    left: 27px;
    top: 56px;
    color: var(--text-light);
    font-size: 16px;
    line-height: 21px;
    letter-spacing: 0.2px;
  }
  .contact__name {
    margin: 0;
    font-size: 22px;
    font-weight: 500;
    letter-spacing: 0.8px;
    line-height: 26px;
  }
  .contact__role { margin: 0 0 16px; }
  .contact__address { margin: 0 0 19px; }
  .contact__list { list-style: none; margin: 0; padding: 0; }
  .contact__list li { display: flex; align-items: center; gap: 10px; }
  .contact__icon { width: 11px; height: 11px; flex: none; }
  .brand {
    position: absolute;
    width: 200px;
    display: flex;
    flex-direction: column;
    align-items: center;
  }
  .brand--front { left: 328px; top: 66px; gap: 9px; }
  .brand--back { left: 182px; top: 56px; gap: 19px; }
  .brand__mark {
    width: 142px;
    height: 142px;
    border-radius: 50%;
    background: var(--brand-purple);
  }
  .brand--back .brand__mark { width: 140px; height: 140px; }
  .brand__name {
    font-size: 40px;
    font-weight: 700;
    line-height: 1;
  }
  .brand--front .brand__name { color: var(--text-dark); }
  .brand--back .brand__name { color: var(--card-light); }
</style>
</head>
<body>
  <section class="card card--front">
    <svg class="front-panel" width="564" height="322" viewBox="0 0 564 322" aria-hidden="true">
      <circle cx="424" cy="161" r="169.5" fill="var(--card-light)"/>
      <circle cx="425.5" cy="161" r="168" fill="var(--brand-purple)"/>
      <circle cx="430" cy="161" r="166" fill="var(--card-light)"/>
      <rect x="430" y="0" width="134" height="322" fill="var(--card-light)"/>
    </svg>
    <div class="contact">
      <h1 class="contact__name">DANIEL REYES</h1>
      <p class="contact__role">Director</p>
      <p class="contact__address">2715 Harbor Lane<br>Coral Bay, FL 33021</p>
      <ul class="contact__list">
        <li><svg class="contact__icon" viewBox="0 0 12 12"><rect x="3" y="0.5" width="6" height="11" rx="1.2" fill="none" stroke="currentColor" stroke-width="1.3"/><line x1="5" y1="9.3" x2="7" y2="9.3" stroke="currentColor" stroke-width="1.2"/></svg>(555) 814-2706</li>
        <li><svg class="contact__icon" viewBox="0 0 12 12"><path d="M2.5 1 L4.5 1 L5.3 3.6 L4 4.6 C4.7 6.2 5.8 7.3 7.4 8 L8.4 6.7 L11 7.5 L11 9.5 C11 10.4 10.3 11 9.5 11 C5.4 10.7 1.3 6.6 1 2.5 C1 1.7 1.6 1 2.5 1 Z" fill="currentColor"/></svg>(555) 639-0472</li>
        <li><svg class="contact__icon" viewBox="0 0 12 12"><rect x="0.8" y="2.3" width="10.4" height="7.4" rx="0.8" fill="none" stroke="currentColor" stroke-width="1.2"/><path d="M1 2.8 L6 6.5 L11 2.8" fill="none" stroke="currentColor" stroke-width="1.2"/></svg>info@Vantiqo.com</li>
        <li><svg class="contact__icon" viewBox="0 0 12 12"><circle cx="6" cy="6" r="5" fill="none" stroke="currentColor" stroke-width="1.1"/><ellipse cx="6" cy="6" rx="2.2" ry="5" fill="none" stroke="currentColor" stroke-width="1"/><line x1="1" y1="6" x2="11" y2="6" stroke="currentColor" stroke-width="1"/></svg>www.Vantiqo.com</li>
      </ul>
    </div>
    <div class="brand brand--front">
      <div class="brand__mark"></div>
      <span class="brand__name">Vantiqo</span>
    </div>
  </section>

  <section class="card card--back">
    <div class="brand brand--back">
      <div class="brand__mark"></div>
      <span class="brand__name">Vantiqo</span>
    </div>
  </section>
</body>
</html>
```